Hallowell Kin Playing Cards

We are wanting a cool design for a playing card that includes our logo(s). I will attach our two logos, we are open to using either one of them or another version of them. I will also attach some pictures of card decks to use for inspiration. These are just decks that we have seen from other artists that we liked. We are located in West Texas so although not necessary, a Sotol or Agave or cactus or quail (bird) or some sort of sunset would pay homage to our surroundings. I realize the examples are all very different, but those are just some decks that we like! Thank you!

```html
<!DOCTYPE html>
<html lang="en">
<head>
<meta charset="UTF-8">
<title>Hallowell Kin Playing Cards</title>
<link href="https://fonts.googleapis.com/css2?family=Oswald:wght@500&family=Rye&display=swap" rel="stylesheet">
<style>
  :root {
    --stage: #e2e2e2;
    --card-black: #0b0b0c;
    --card-face: #161617;
    --pattern-deep: #06152e;
    --pattern-mid: #1560c4;
    --pattern-light: #2f8ee6;
    --silver: #d6d6d2;
    --silver-dim: #8d8a80;
    --badge-blue: #1f74d8;
  }
  * { margin: 0; padding: 0; box-sizing: border-box; }
  html, body { width: 1200px; height: 958px; overflow: hidden; background: var(--stage); }
  .stage { position: relative; width: 1200px; height: 958px; }

  .card {
    position: absolute;
    top: 171px;
    width: 440px;
    height: 616px;
    border-radius: 26px;
    background: var(--card-black);
    box-shadow: 0 12px 30px rgba(0,0,0,0.18);
  }
  .card--back { left: 140px; }
  .card--face { left: 620px; background: linear-gradient(160deg, #2a2a2c 0%, var(--card-face) 45%, #050506 100%); }

  .back-pattern {
    position: absolute;
    inset: 10px;
    border-radius: 20px;
    background:
      radial-gradient(circle at 50% 50%, rgba(6,21,46,0.55) 0%, transparent 35%),
      radial-gradient(ellipse at 80% 15%, var(--pattern-light) 0%, transparent 45%),
      radial-gradient(ellipse at 20% 85%, var(--pattern-light) 0%, transparent 45%),
      linear-gradient(135deg, var(--pattern-deep) 0%, var(--pattern-mid) 40%, var(--pattern-mid) 60%, var(--pattern-deep) 100%);
  }
  .brand-plate {
    position: absolute;
    left: 50%;
    top: 50%;
    transform: translate(-50%, -50%);
    display: flex;
    align-items: center;
    gap: 12px;
    padding: 16px 26px;
    background: var(--card-black);
    border-radius: 10px;
  }
  .brand-plate__dot {
    width: 18px; height: 18px; border-radius: 50%;
    background: var(--badge-blue);
  }
  .brand-plate__name {
    font-family: 'Oswald', sans-serif;
    font-weight: 500;
    font-size: 34px;
    letter-spacing: 1px;
    text-transform: uppercase;
    color: var(--silver);
    white-space: nowrap;
  }

  .face-frame {
    position: absolute;
    inset: 18px;
    border: 2px solid var(--silver-dim);
    border-radius: 16px;
  }
  .index {
    position: absolute;
    display: flex;
    flex-direction: column;
    align-items: center;
    color: var(--silver);
    background: transparent;
  }
  .index--top { top: 34px; left: 34px; }
  .index--bottom { bottom: 34px; right: 34px; transform: rotate(180deg); }
  .index__rank { font-family: 'Rye', serif; font-size: 52px; line-height: 1; }
  .index__suit { font-family: 'Oswald', sans-serif; font-size: 40px; line-height: 1.1; }

  .center-pip {
    position: absolute;
    left: 50%;
    top: 50%;
    width: 280px;
    height: 280px;
    transform: translate(-50%, -50%);
  }
</style>
</head>
<body>
<main class="stage">
  <section class="card card--back" aria-label="Card back">
    <div class="back-pattern" role="img" aria-label="Blue and black ornamental mandala pattern covering the card back"></div>
    <div class="brand-plate">
      <span class="brand-plate__dot"></span>
      <span class="brand-plate__name">Hallowell Kin</span>
    </div>
  </section>

  <section class="card card--face" aria-label="Ace of clubs">
    <div class="face-frame"></div>
    <div class="index index--top">
      <span class="index__rank">A</span>
      <span class="index__suit">♣</span>
    </div>
    <svg class="center-pip" viewBox="0 0 280 280" role="img" aria-label="Large ornate silver club illustration with paisley and feather detailing">
      <defs>
        <radialGradient id="pipSilver" cx="50%" cy="40%" r="60%">
          <stop offset="0%" stop-color="#f0f0ec"/>
          <stop offset="55%" stop-color="#b4b3ad"/>
          <stop offset="100%" stop-color="#6e6d68"/>
        </radialGradient>
      </defs>
      <g fill="url(#pipSilver)">
        <circle cx="140" cy="78" r="62"/>
        <circle cx="72" cy="168" r="62"/>
        <circle cx="208" cy="168" r="62"/>
        <path d="M128 150 L152 150 L170 262 L110 262 Z"/>
      </g>
    </svg>
    <div class="index index--bottom">
      <span class="index__rank">A</span>
      <span class="index__suit">♣</span>
    </div>
  </section>
</main>
</body>
</html>
```